Business Card Design for company

We want new business cards. We'd like something different-- yet still highly professional. Our tagline is Providing leadership, delivering success. Stock photos are ok, as long as they are relevant and look upscale.

Target Market(s)

Architecture/Business Management Consulting/Engineering Consulting

Contact Information for Business Card

dark gray background with pops of blue might be good, but you tell me. You're the designers. Rounded corners might be nice, but again, you tell me.

Font styles to use
Serif
Sans Serif

Colors
3276b5
5c5c5c
9d9d9d
fbfbfb

Requirements
Nice to have
• Something different, but still very professional.

```html
<!DOCTYPE html>
<html lang="en">
<head>
<meta charset="utf-8">
<title>Velar International — Business Card</title>
<link rel="stylesheet" href="https://fonts.googleapis.com/css2?family=Open+Sans:wght@400;600&display=swap">
<style>
  :root {
    --blue: #3276b5;
    --blue-deep: #2a64a0;
    --sky: #4ab3da;
    --gray-dark: #5c5c5c;
    --gray-mid: #9d9d9d;
    --gray-light: #c9c9c9;
    --paper: #fbfbfb;
    --stage: #e7e5e2;
  }
  * { margin: 0; padding: 0; box-sizing: border-box; }
  html, body {
    width: 1200px;
    height: 1023px;
    overflow: hidden;
    background: var(--stage);
    font-family: "Open Sans", Arial, sans-serif;
  }
  .sheet {
    width: 1200px;
    height: 1023px;
    display: flex;
    flex-direction: column;
    align-items: center;
    justify-content: space-evenly;
  }
  .card {
    position: relative;
    width: 820px;
    height: 469px;
    background: var(--paper);
    box-shadow: 0 6px 18px rgba(0, 0, 0, 0.14);
    overflow: hidden;
  }
  .card-art {
    position: absolute;
    inset: 0;
    width: 100%;
    height: 100%;
  }
  .brand {
    position: absolute;
    left: 70px;
    top: 180px;
    display: flex;
    align-items: center;
    gap: 18px;
  }
  .brand-square {
    width: 22px;
    height: 22px;
    background: var(--blue);
  }
  .brand-name {
    font-weight: 600;
    font-size: 40px;
    line-height: 1.1;
    color: var(--blue);
    letter-spacing: 0.5px;
  }
  .identity {
    position: absolute;
    left: 590px;
    top: 78px;
    color: #fff;
  }
  .person-name {
    font-weight: 600;
    font-size: 30px;
    line-height: 1.1;
  }
  .person-role {
    font-weight: 400;
    font-size: 18px;
    margin-top: 2px;
  }
  .contact-list {
    position: absolute;
    left: 590px;
    top: 222px;
    list-style: none;
    color: #fff;
    font-size: 17px;
    line-height: 1.3;
  }
  .contact-item {
    display: flex;
    align-items: flex-start;
    gap: 10px;
    margin-bottom: 6px;
  }
  .contact-icon {
    flex: 0 0 18px;
    width: 18px;
    height: 18px;
    margin-top: 3px;
  }
</style>
</head>
<body>
<main class="sheet">

  <section class="card card-front" aria-label="Card front">
    <svg class="card-art" viewBox="0 0 820 469" aria-hidden="true">
      <defs>
        <linearGradient id="front-blue" x1="0" y1="0" x2="1" y2="1">
          <stop offset="0" stop-color="#2f70ae"/>
          <stop offset="1" stop-color="#245b95"/>
        </linearGradient>
        <linearGradient id="front-band" x1="0" y1="0" x2="0" y2="1">
          <stop offset="0" stop-color="#b5b5b5"/>
          <stop offset="1" stop-color="#d6d6d6"/>
        </linearGradient>
      </defs>
      <circle cx="1010" cy="250" r="540" fill="url(#front-band)"/>
      <circle cx="1010" cy="250" r="505" fill="#5c5c5c"/>
      <circle cx="1010" cy="250" r="485" fill="url(#front-blue)"/>
    </svg>

    <div class="brand">
      <span class="brand-square"></span>
      <span class="brand-name">Velar<br>International</span>
    </div>

    <div class="identity">
      <p class="person-name">Owen Marsh</p>
      <p class="person-role">Owner</p>
    </div>

    <ul class="contact-list">
      <li class="contact-item">
        <svg class="contact-icon" viewBox="0 0 18 18" aria-hidden="true">
          <rect width="18" height="18" rx="3" fill="#fff"/>
          <path d="M5 4.5c.6-.6 1.3-.5 1.7.1l1 1.5c.3.5.2 1-.2 1.4l-.6.5c.6 1.2 1.6 2.3 2.9 2.9l.5-.6c.4-.4.9-.5 1.4-.2l1.5 1c.6.4.7 1.1.1 1.7-.9.9-2.2 1.1-3.4.5C7.6 12.3 5.7 10.4 4.7 8.1c-.5-1.2-.4-2.6.3-3.6z" fill="var(--blue)"/>
        </svg>
        <span>+0000-0000-0000</span>
      </li>
      <li class="contact-item">
        <svg class="contact-icon" viewBox="0 0 18 18" aria-hidden="true">
          <rect width="18" height="18" rx="3" fill="#fff"/>
          <rect x="3.5" y="5" width="11" height="8" fill="none" stroke="var(--blue)" stroke-width="1.5"/>
          <path d="M3.5 5l5.5 4.5L14.5 5" fill="none" stroke="var(--blue)" stroke-width="1.5"/>
        </svg>
        <span>info@yourdomain.com</span>
      </li>
      <li class="contact-item">
        <svg class="contact-icon" viewBox="0 0 18 18" aria-hidden="true">
          <rect width="18" height="18" rx="3" fill="#fff"/>
          <circle cx="9" cy="9" r="5.2" fill="none" stroke="var(--blue)" stroke-width="1.4"/>
          <path d="M3.8 9h10.4M9 3.8c-2 2.8-2 7.6 0 10.4M9 3.8c2 2.8 2 7.6 0 10.4" fill="none" stroke="var(--blue)" stroke-width="1.1"/>
        </svg>
        <span>www.yourdomain.com</span>
      </li>
      <li class="contact-item">
        <svg class="contact-icon" viewBox="0 0 18 18" aria-hidden="true">
          <rect width="18" height="18" rx="3" fill="#fff"/>
          <path d="M9 3.5a3.8 3.8 0 0 0-3.8 3.8c0 2.8 3.8 7.2 3.8 7.2s3.8-4.4 3.8-7.2A3.8 3.8 0 0 0 9 3.5z" fill="var(--blue)"/>
          <circle cx="9" cy="7.3" r="1.4" fill="#fff"/>
        </svg>
        <span>Studio 12,<br>48 Larkfield Row,<br>London</span>
      </li>
    </ul>
  </section>

  <section class="card card-back" aria-label="Card back">
    <svg class="card-art" viewBox="0 0 820 469" aria-hidden="true">
      <defs>
        <linearGradient id="back-sky" x1="0" y1="1" x2="1" y2="0">
          <stop offset="0" stop-color="#4ab3da"/>
          <stop offset="1" stop-color="#2f70ae"/>
        </linearGradient>
        <linearGradient id="back-band" x1="0" y1="0" x2="0" y2="1">
          <stop offset="0" stop-color="#bdbdbd"/>
          <stop offset="1" stop-color="#d9d9d9"/>
        </linearGradient>
      </defs>
      <circle cx="1010" cy="250" r="540" fill="url(#back-band)"/>
      <circle cx="1010" cy="250" r="505" fill="#5c5c5c"/>
      <circle cx="1010" cy="250" r="485" fill="url(#back-sky)"/>
    </svg>
  </section>

</main>
</body>
</html>
```